life insurance quote website design for lepontdoriole.ca

the web site lepontdoriole.ca need a design. we dont like the actuel one but we are open at all new suggestion. visit us at lepontdoriole.ca and you will understand. the principal concurant is tarifsgarantisnord.ca, calculeo.ca, coutprotecfam.ca. We are a life insurance quote site. we found best price available in the canadien industrie. We absolutly want a design with our form in the front page on the top right side like our concurance, we use wordpress at this time. we want to be able to switch language. and to have a logic form. we want to be able to change the color for each type of insurance quote page.we also need a blog in it to post news. and the site will be SEO accurate.

Target Market(s)

Get client fill the quote form

Industry/Entity Type

Insurance

Number of Pages Required

3 page

Font styles to use
Sans Serif

Requirements
Must have
• logic form on the top right first page
• page template for product info stuff, contact, and who we are, blog
• French site
• custum color
Nice to have
• Wordpress design will be appréciate
• switch language english/french

```html
<!DOCTYPE html>
<html lang="fr">
<head>
<meta charset="utf-8">
<title>lepontdoriole.ca — Assurance vie</title>
<link rel="stylesheet" href="https://fonts.googleapis.com/css2?family=Open+Sans:wght@400;600;700&family=Oswald:wght@400;500&display=swap">
<style>
:root{
  --red:#d71920;
  --red-dark:#b3141a;
  --blue:#1f73b7;
  --blue-head:#1d63a6;
  --navy:#0f2a44;
  --ink:#333;
  --muted:#777;
  --line:#e2e2e2;
  --gray-bg:#f3f3f3;
  --footer:#242424;
  --footer-text:#c9c9c9;
  --white:#fff;
}
*{box-sizing:border-box;margin:0;padding:0}
html,body{width:1200px;height:2320px;overflow:hidden}
body{position:relative;font-family:"Open Sans",Arial,sans-serif;color:var(--ink);background:var(--white);font-size:13px}
.abs{position:absolute}

/* header */
.top-line{left:0;top:0;width:1200px;height:5px;background:var(--red)}
.brand{left:98px;top:40px;display:flex;align-items:center;gap:10px}
.brand-mark{width:28px;height:28px;border-radius:50%;background:var(--red)}
.brand-name{font-size:22px;font-weight:700;color:var(--red)}
.call{left:750px;top:38px;display:flex;gap:12px;align-items:center}
.call-icon{width:38px;height:38px;border:2px solid var(--red);border-radius:50%;display:flex;align-items:center;justify-content:center}
.call-title{color:var(--red);font-size:14px}
.call-num{color:#666;font-size:12px;margin-top:3px}
.lang{left:955px;top:40px;width:146px;height:39px;border:1px solid #ddd;display:flex;align-items:center;padding:0 16px;gap:12px;font-size:13px;color:#555}
.flag{width:22px;height:13px;background:linear-gradient(#23407a,#c8102e)}

/* nav */
.nav{left:0;top:117px;width:1200px;height:47px;background:var(--red);border-bottom:2px solid var(--red-dark)}
.nav ul{position:absolute;left:99px;top:0;display:flex;list-style:none;height:45px}
.nav li{height:45px;display:flex;align-items:center;justify-content:center;color:#fff;font-size:11px;font-weight:600;text-transform:uppercase;border-right:1px solid rgba(255,255,255,.25)}
.nav li.active{background:var(--navy)}

/* hero */
.hero{left:0;top:164px;width:1200px;height:447px;background:radial-gradient(circle at 20% 30%,#5e7fa6 0,#1d3250 45%,#0c1828 100%)}
.hero-frame{left:105px;top:207px;width:702px;height:326px;border:4px solid #b8c2cc;background:linear-gradient(180deg,#4d8fd6,#9cc8ef 70%,#7b93a7)}
.dots{left:568px;top:568px;display:flex;gap:8px}
.dots span{width:10px;height:10px;border-radius:50%;background:#e05550}
.dots span.on{background:#fff}

/* quote form */
.quote{left:807px;top:117px;width:294px;height:664px;background:#fff;box-shadow:0 2px 8px rgba(0,0,0,.15)}
.quote-head{height:47px;background:var(--blue);color:#fff;font-size:15px;display:flex;align-items:center;justify-content:center}
.quote-body{padding:14px 31px}
.q-label{font-size:14px;font-weight:600;color:#333;margin:8px 0 10px}
.field{height:36px;border:1px solid #ddd;margin-bottom:12px;display:flex;align-items:center;padding:0 12px;gap:10px;font-size:11px;color:#999}
.field.select{justify-content:space-between}
.ico{width:10px;height:10px;background:#bbb;border-radius:2px}
.check-row{display:flex;align-items:flex-start;gap:8px;font-size:10px;color:#999;margin-bottom:12px;line-height:1.5}
.box{width:10px;height:10px;border:1px solid #bbb;flex:none;margin-top:2px}
.gender{display:flex;gap:10px;align-items:center;font-size:11px;color:#555;margin-bottom:20px}
.gender span.opt{display:flex;gap:5px;align-items:center;color:#999;font-size:10px}
.captcha{display:flex;gap:20px;align-items:center;margin:6px 0 24px}
.captcha-img{width:80px;height:24px;background:linear-gradient(90deg,#cfcfcf,#9a9a9a,#cfcfcf)}
.captcha-in{width:112px;height:36px;border:1px solid #ddd}
.send{height:44px;background:linear-gradient(#3b95de,#1c6cb4);border-radius:4px;color:#fff;font-size:12px;font-weight:600;display:flex;align-items:center;justify-content:center;box-shadow:0 2px 0 #154f85}

/* services */
.tagline{left:0;top:636px;width:1200px;text-align:center;padding-right:10px;font-family:"Oswald",Arial,sans-serif;font-size:31px;font-weight:400;color:var(--blue-head)}
.tagline span{margin-left:-18px}
.slide-arrow{top:790px;width:16px;height:40px}
.service{top:732px;width:240px;text-align:center}
.service .ring{width:160px;height:160px;border-radius:50%;margin:0 auto;border:5px solid}
.service h3{margin-top:18px;font-size:15px;font-weight:600;color:var(--blue-head)}
.service p{margin-top:10px;font-size:12px;color:#777;line-height:1.75}

/* blog area */
.gray{left:0;top:1020px;width:1200px;height:1021px;background:var(--gray-bg)}
.sec-title{left:98px;top:1046px;font-family:"Oswald",Arial,sans-serif;font-size:21px;font-weight:500;color:var(--red)}
.mini-nav{left:724px;top:1053px;display:flex;gap:3px}
.mini-nav span{width:20px;height:20px;background:#ddd}
.card{background:#fff;border:1px solid #ddd;box-shadow:0 1px 3px rgba(0,0,0,.08)}
.card-in{padding:26px 28px 0}
.card h2{font-size:16px;font-weight:700;color:var(--blue-head);text-transform:uppercase}
.card .lead{margin-top:10px;font-size:13px;color:#777;line-height:1.95}
.list{display:grid;grid-template-columns:385px 230px;row-gap:16px;margin-top:18px}
.list div{display:flex;align-items:center;gap:14px;font-size:13px;color:#444}
.num{width:24px;height:24px;border-radius:50%;background:var(--red);color:#fff;font-size:11px;font-weight:700;display:flex;align-items:center;justify-content:center}
.meta{display:flex;gap:28px;font-size:11px;color:#777;margin-top:14px}
.meta b{font-weight:400;color:var(--blue)}
.body{margin-top:14px;font-size:13px;color:#777;line-height:1.95}
.share{position:absolute;left:0;bottom:0;width:100%;height:43px;border-top:1px solid var(--line);display:flex}
.share span{width:76px;border-right:1px solid var(--line);display:flex;align-items:center;justify-content:center}
.share span i{width:9px;height:9px;border-radius:50%;background:#444}
.share .more{width:auto;flex:1;border:none;justify-content:flex-start;padding-left:44px;color:var(--blue);font-size:13px;text-decoration:underline}

/* sidebar */
.side h4{position:absolute;left:17px;top:18px;font-size:15px;font-weight:700;color:var(--blue-head);text-transform:uppercase}
.post{position:absolute;left:16px;display:flex;gap:12px}
.thumb{width:92px;height:80px;border:3px solid #eee;flex:none}
.post-text{white-space:nowrap}
.post-title{display:block;color:var(--blue);font-size:12.5px;line-height:1.3}
.post em{display:block;color:var(--blue);font-size:10px;margin:2px 0 7px}
.post p{font-size:9px;color:#777;line-height:1.9}
.office-row{position:absolute;left:30px;display:flex;gap:14px;font-size:12px;color:#555}
.chev{color:var(--blue);font-weight:700}
.addr{position:absolute;left:58px;top:88px;font-size:12px;color:#888;line-height:1.8}
.towns{position:absolute;left:58px;top:142px;font-weight:600;font-size:12px;color:#333}
.hours{position:absolute;left:19px;top:50px;font-size:12px;color:#555;line-height:2.2}

/* footer */
.footer{left:0;top:2041px;width:1200px;height:225px;background:var(--footer)}
.f-col{top:2076px;color:var(--footer-text)}
.f-col h5{font-size:15px;font-weight:400;color:#fff;padding-bottom:12px;border-bottom:1px dotted #777;margin-bottom:16px}
.f-col ul{list-style:none;font-size:11px;line-height:2.1}
.f-col ul li::before{content:"›";margin-right:10px}
.f-col p{font-size:11px;line-height:1.85}
.f-contact div{display:flex;gap:12px;align-items:center;font-size:11px;margin-top:14px}
.member{left:892px;top:2096px;width:200px;height:90px;background:#333;border:1px solid #555}
.bottom{left:0;top:2266px;width:1200px;height:54px;background:var(--red);color:#fff;font-size:11px}
.copy{position:absolute;left:98px;top:19px}
.socials{position:absolute;left:950px;top:14px;display:flex;gap:8px}
.socials span{width:24px;height:24px;border:2px solid #fff;border-radius:50%}
</style>
</head>
<body>

<div class="abs top-line"></div>

<header>
  <div class="abs brand"><span class="brand-mark"></span><span class="brand-name">lepontdoriole.ca</span></div>
  <div class="abs call">
    <div class="call-icon">
      <svg width="16" height="16" viewBox="0 0 24 24"><path d="M6.6 10.8a15 15 0 0 0 6.6 6.6l2.2-2.2a1 1 0 0 1 1-.25 11 11 0 0 0 3.6.6 1 1 0 0 1 1 1V20a1 1 0 0 1-1 1A17 17 0 0 1 3 4a1 1 0 0 1 1-1h3.5a1 1 0 0 1 1 1c0 1.25.2 2.45.6 3.6a1 1 0 0 1-.25 1z" fill="#d71920"/></svg>
    </div>
    <div><div class="call-title">Call Now :</div><div class="call-num">1-855-555-0142</div></div>
  </div>
  <div class="abs lang"><span class="flag"></span><span>English</span>
    <svg width="9" height="6" viewBox="0 0 9 6"><path d="M1 1l3.5 3.5L8 1" stroke="#777" fill="none"/></svg>
  </div>
</header>

<nav class="abs nav">
  <ul>
    <li class="active" style="width:111px">Home</li>
    <li style="width:119px">Products</li>
    <li style="width:135px">Submission</li>
    <li style="width:88px">Blog</li>
    <li style="width:133px">Who we are</li>
    <li style="width:122px">Contact us</li>
  </ul>
</nav>

<section class="abs hero"></section>
<div class="abs hero-frame" role="img" aria-label="Slide photo: family playing outdoors under a blue sky beside the insurance badge"></div>
<div class="abs dots"><span></span><span class="on"></span><span></span><span></span></div>

<form class="abs quote">
  <div class="quote-head">Quote Request</div>
  <div class="quote-body">
    <div class="q-label">Product</div>
    <div class="field select"><span>Select...</span>
      <svg width="8" height="5" viewBox="0 0 8 5"><path d="M1 1l3 3 3-3" stroke="#777" fill="none"/></svg></div>
    <div class="q-label" style="margin-top:22px">Applicant</div>
    <div class="field"><span class="ico"></span>Full Name *</div>
    <div class="field"><span class="ico"></span>Cities *</div>
    <div class="field"><span class="ico"></span>Email *</div>
    <div class="field"><span class="ico"></span>Phone *</div>
    <div class="gender">Gender * <span class="opt"><span class="box"></span>Man</span><span class="opt"><span class="box"></span>Woman</span></div>
    <div class="q-label">Co-Applicant</div>
    <div class="check-row"><span class="box"></span>Add a co-applicant</div>
    <div class="check-row"><span class="box"></span>I HAVE READ AND ACCEPT THE USE AND PRIVACY POLICY OF **</div>
    <div class="captcha"><span class="captcha-img" role="img" aria-label="Security code image"></span><span class="captcha-in"></span></div>
    <div class="send">TO SEND</div>
  </div>
</form>

<h1 class="abs tagline"><span>L'assurance d'obtenir le meilleur prix</span></h1>

<svg class="abs slide-arrow" style="left:58px" viewBox="0 0 16 40"><path d="M14 2L3 20l11 18" stroke="#ccc" fill="none" stroke-width="1.5"/></svg>
<svg class="abs slide-arrow" style="left:1126px" viewBox="0 0 16 40"><path d="M2 2l11 18L2 38" stroke="#ccc" fill="none" stroke-width="1.5"/></svg>

<div class="abs service" style="left:112px">
  <div class="ring" role="img" aria-label="Illustration of a family in front of a house on green grass" style="border-color:#2fa4d8;background:linear-gradient(#bfe5f6,#8bcf5a)"></div>
  <h3>ASSURANCE VIE</h3><p>Que vous soyez à la recherche<br>d'une assurance vie</p>
</div>
<div class="abs service" style="left:359px">
  <div class="ring" role="img" aria-label="Photo of stacked coins" style="border-color:#e8a53a;background:radial-gradient(#e9c07a,#9a6a2e)"></div>
  <h3>SALARIE</h3><p>Que vous soyez à la recherche<br>d'une assurance vie</p>
</div>
<div class="abs service" style="left:600px">
  <div class="ring" role="img" aria-label="Photo of a homeowner at her door" style="border-color:#55b548;background:linear-gradient(#e7e1d6,#b9a58c)"></div>
  <h3>HYPOTHECAIRE</h3><p>Que vous soyez à la recherche<br>d'une assurance vie</p>
</div>
<div class="abs service" style="left:848px">
  <div class="ring" role="img" aria-label="Photo of two hands clasped in support" style="border-color:#d9476a;background:radial-gradient(#c9967c,#6e4634)"></div>
  <h3>MALADIES GRAVES</h3><p>Que vous soyez à la recherche<br>d'une assurance vie</p>
</div>

<section class="abs gray"></section>
<h2 class="abs sec-title">OUR LATEST BLOG POST</h2>
<div class="abs mini-nav"><span></span><span></span></div>

<article class="abs card" style="left:97px;top:1098px;width:678px;height:270px">
  <div class="card-in">
    <h2>Find the best insurance at the best price!</h2>
    <p class="lead">Whether you are looking for life insurance, mortgage insurance or else you certainly want to pay the most advantageous price. Navigating among the many offers</p>
    <div class="list">
      <div><span class="num">1</span>Permanent life insurance - term life insurance</div>
      <div><span class="num">4</span>Critical illness insurance</div>
      <div><span class="num">2</span>Disability Insurance - Disability insurance</div>
      <div></div>
      <div><span class="num">3</span>Mortgage Insurance - loans</div>
    </div>
  </div>
</article>

<article class="abs card" style="left:97px;top:1410px;width:678px;height:272px">
  <div class="card-in">
    <h2>Comment procéder?</h2>
    <div class="meta"><span>Published in <b>insurance</b></span><span>Written by <b>Admin</b></span><span>Comments <b>277</b></span></div>
    <p class="body">Lepontdoriole .ca vous offre un service novateur dans le domaine de l'assurance. Grâce à nos méthodes éprouvées et à notre compétence, vous êtes assurés de trouver ce que vous cherchez, et même plus. Non seulement nous avons accès aux produits des assureurs les plus reconnus et les plus importants du Canada, mais de plus, nos conseillers</p>
  </div>
  <div class="share"><span><i></i></span><span><i></i></span><span><i></i></span><span><i></i></span><span><i></i></span><span><i></i></span><span class="more">Read More</span></div>
</article>

<article class="abs card" style="left:97px;top:1722px;width:678px;height:272px">
  <div class="card-in">
    <h2>Des conseillers en sécurité financière compétents</h2>
    <div class="meta"><span>Published in <b>insurance</b></span><span>Written by <b>Admin</b></span><span>Comments <b>277</b></span></div>
    <p class="body">Lepontdoriole .ca vous offre un service novateur dans le domaine de l'assurance. Grâce à nos méthodes éprouvées et à notre compétence, vous êtes assurés de trouver ce que vous cherchez, et même plus. Non seulement nous avons accès aux produits des assureurs les plus reconnus et les plus importants du Canada, mais de plus, nos conseillers</p>
  </div>
  <div class="share"><span><i></i></span><span><i></i></span><span><i></i></span><span><i></i></span><span><i></i></span><span><i></i></span><span class="more">Read More</span></div>
</article>

<aside class="abs card side" style="left:816px;top:1098px;width:285px;height:284px">
  <h4>How to proceed?</h4>
  <div class="post" style="top:58px"><span class="thumb" role="img" aria-label="Photo of a smiling family" style="background:linear-gradient(#c9d8b4,#8aa86a)"></span>
    <div class="post-text"><span class="post-title">Insurance: ? How to find</span><em>02 Dec 2016</em><p>Life insurance market premium<br>may seem complex at first.</p></div></div>
  <div class="post" style="top:170px"><span class="thumb" role="img" aria-label="Photo of a hand holding an insurance card" style="background:linear-gradient(#e6e6ea,#9aa0ad)"></span>
    <div class="post-text"><span class="post-title">Competent financial</span><em>02 Dec 2016</em><p>Life insurance market premium<br>may seem complex at first.</p></div></div>
</aside>

<aside class="abs card side" style="left:816px;top:1421px;width:285px;height:392px">
  <h4>Our offices</h4>
  <div class="office-row" style="top:64px"><span class="chev">»</span>The head office</div>
  <div class="addr">48 Maple Lane, La Prairie,<br>QC, J5R 0A1</div>
  <div class="towns">TOWNS</div>
  <div class="office-row" style="top:177px"><span class="chev">»</span>Quebec</div>
  <div class="office-row" style="top:213px"><span class="chev">»</span>Sherbrooke</div>
  <div class="office-row" style="top:249px"><span class="chev">»</span>Granby</div>
  <div class="office-row" style="top:285px"><span class="chev">»</span>Beauce</div>
  <div class="office-row" style="top:321px"><span class="chev">»</span>three Rivères</div>
  <div class="office-row" style="top:357px"><span class="chev">»</span>Piedmont</div>
</aside>

<aside class="abs card side" style="left:816px;top:1850px;width:285px;height:144px">
  <h4>Hours of operation</h4>
  <div class="hours">Monday to Friday: 7am to 21hrs<br>Sunday: 10hrs to 15hrs<br>Toll free: 1-855-555-0142</div>
</aside>

<footer class="abs footer"></footer>
<div class="abs f-col" style="left:98px;width:128px">
  <h5>Quick Links</h5>
  <ul><li>Home</li><li>About Us</li><li>Services</li><li>News</li><li>Contacts</li></ul>
</div>
<div class="abs f-col" style="left:313px;width:228px">
  <h5>Informations</h5>
  <p>Disbursing monthly or annually money for insurance is considerable expense. Even if your payments do not</p>
</div>
<div class="abs f-col f-contact" style="left:596px;width:202px">
  <h5>Contact Infomation</h5>
  <p>Address Name : Street Name , City Name, Country Name, 7895663.</p>
  <div><svg width="12" height="12" viewBox="0 0 24 24"><path d="M6.6 10.8a15 15 0 0 0 6.6 6.6l2.2-2.2a1 1 0 0 1 1-.25 11 11 0 0 0 3.6.6 1 1 0 0 1 1 1V20a1 1 0 0 1-1 1A17 17 0 0 1 3 4a1 1 0 0 1 1-1h3.5a1 1 0 0 1 1 1c0 1.25.2 2.45.6 3.6a1 1 0 0 1-.25 1z" fill="#ccc"/></svg>1-855-555-0142</div>
  <div><svg width="13" height="10" viewBox="0 0 13 10"><rect x=".5" y=".5" width="12" height="9" fill="none" stroke="#ccc"/><path d="M.5.5l6 5 6-5" stroke="#ccc" fill="none"/></svg>info@lepontdoriole.ca</div>
</div>
<div class="abs member" role="img" aria-label="Professional membership badge"></div>

<div class="abs bottom">
  <span class="copy">Copyright © 2016lepontdoriole.ca</span>
  <div class="socials"><span></span><span></span><span></span><span></span><span></span></div>
</div>

</body>
</html>
```